Harborview Estates Business Card for Apartment Buildings

Create business cards for resident managers who run apartment buildings. The audience is the public who are searching for apartment rentals, and current residents who live at the apartment building. Key design element will be incorporating the company logo, however, the logo cannot dominate. The building name and manager name are more important than the logo. Current business card design leaves little room for copy, so we may need to reduce the size on the current card to allow for more space for copy.

Target Market(s)

Adults 18-65 years of age, who are looking for an apartment rental, plus current residents who live at our apartment buildings.

Industry/Entity Type

Property Management

Contact Information for Business Card

A major design element will be use of the company logo. Important property and manager contact information must be part of the design. The size of the logo will need to be reduced to make room for building and manager contact copy.

Font styles to use
Sans Serif

Colors
3176b5
000000
959595
ffffff

Requirements
Must have
• 1) Incorporate the company logo.
• 2) Use the company colors (dark blue, black/grey, over white).
• 3) FEATURE THE BUILDING NAME
• 4) FEATURE THE MANAGER NAME
• 5) The company name is less important than BUILDING and MANAGER
• 6) Manager contact information
• **SEE ATTACHED CREATIVE BRIEF**
Nice to have
• 1) Back of card logo watermark
• 2) Ability to write notes on back of carfd
Should not have
• Avoid letting the company logo dominate the card, the building name and manager are more important than the company logo.

```html
<!DOCTYPE html>
<html lang="en">
<head>
<meta charset="UTF-8">
<title>Harborview Estates – Resident Manager Card</title>
<link href="https://fonts.googleapis.com/css2?family=Work+Sans:wght@400;500;600;700&display=swap" rel="stylesheet">
<style>
  :root {
    --brand-blue: #3176b5;
    --ink: #000000;
    --slate: #3d3e40;
    --slate-deep: #303133;
    --mid-grey: #959595;
    --paper: #ffffff;
    --stage: #e6e7e9;
  }
  * { margin: 0; padding: 0; box-sizing: border-box; }
  html, body { width: 1200px; height: 900px; overflow: hidden; }
  body {
    background: var(--stage);
    font-family: "Work Sans", Arial, sans-serif;
    position: relative;
  }
  .card {
    position: absolute;
    left: 280px;
    width: 640px;
    height: 366px;
    border-radius: 16px;
    overflow: hidden;
  }
  .card-front { top: 40px; background: var(--paper); }
  .card-back { top: 494px; background: var(--slate-deep); }

  .front-shape { position: absolute; inset: 0; }

  .company-mark {
    position: absolute; left: 40px; top: 38px;
    display: flex; align-items: center; gap: 10px;
  }
  .company-mark .mark-square {
    width: 20px; height: 20px; background: var(--brand-blue);
  }
  .company-mark .mark-name {
    color: var(--brand-blue); font-weight: 700; font-size: 22px;
    letter-spacing: 0.5px;
  }

  .property { position: absolute; left: 40px; top: 102px; }
  .property-name { color: var(--brand-blue); font-size: 18px; font-weight: 500; }
  .property-address { color: var(--slate); font-size: 15px; margin-top: 4px; }

  .manager {
    position: absolute; right: 40px; top: 140px; text-align: right;
  }
  .manager-name {
    color: var(--brand-blue); font-size: 25px; font-weight: 500;
    text-transform: uppercase; letter-spacing: 0.5px;
  }
  .manager-title { color: var(--slate); font-size: 15px; margin-top: 2px; }
  .accent-bar {
    position: absolute; right: 0; top: 142px; width: 16px; height: 50px;
    background: var(--brand-blue);
  }

  .contact-list {
    position: absolute; left: 40px; top: 216px; list-style: none;
  }
  .contact-list li {
    display: flex; align-items: center; gap: 12px;
    color: var(--paper); font-size: 14.5px; height: 25px;
  }
  .contact-list svg { width: 12px; height: 12px; fill: var(--paper); flex: none; }

  .back-wordmark {
    position: absolute; left: 0; right: 0; top: 130px; text-align: center;
  }
  .back-name {
    color: #d9dadb; font-size: 46px; font-weight: 700; letter-spacing: 1px;
  }
  .back-url {
    color: #d9dadb; font-size: 18px; margin-top: 18px; letter-spacing: 0.5px;
  }
</style>
</head>
<body>

<section class="card card-front" aria-label="Business card front">
  <svg class="front-shape" viewBox="0 0 640 366" preserveAspectRatio="none" aria-hidden="true">
    <path d="M0 196 H470 C410 236 392 300 410 366 H0 Z" fill="var(--slate)"/>
  </svg>

  <div class="company-mark">
    <span class="mark-square"></span>
    <span class="mark-name">HARBORVIEW ESTATES LLC</span>
  </div>

  <div class="property">
    <p class="property-name">Cedar Court Apartments</p>
    <p class="property-address">2450 Linden Avenue Fairview, CA 90210</p>
  </div>

  <div class="manager">
    <p class="manager-name">Marisol Vega</p>
    <p class="manager-title">Resident Manager</p>
  </div>
  <span class="accent-bar"></span>

  <ul class="contact-list">
    <li>
      <svg viewBox="0 0 12 12"><path d="M2.5 0.5 L4.5 0.5 L5 3 L3.6 4 C4.3 5.8 6 7.6 8 8.4 L9 7 L11.5 7.5 L11.5 9.5 C11.5 10.8 10.5 11.5 9.5 11.5 C4.8 11 1 7.2 0.5 2.5 C0.5 1.5 1.2 0.5 2.5 0.5 Z"/></svg>
      <span>555-014-2210</span>
    </li>
    <li>
      <svg viewBox="0 0 12 12"><path d="M3 0 H9 A1 1 0 0 1 10 1 V11 A1 1 0 0 1 9 12 H3 A1 1 0 0 1 2 11 V1 A1 1 0 0 1 3 0 Z M3.5 1.5 V9.5 H8.5 V1.5 Z"/></svg>
      <span>555-018-4473</span>
    </li>
    <li>
      <svg viewBox="0 0 12 12"><path d="M3 0 H9 V3 H3 Z M0.5 4 H11.5 V9 H9.5 V7 H2.5 V9 H0.5 Z M3 8 H9 V12 H3 Z"/></svg>
      <span>555-016-9050</span>
    </li>
    <li>
      <svg viewBox="0 0 12 12"><path d="M0 2 H12 V10 H0 Z M1 3 L6 6.5 L11 3 Z" fill-rule="evenodd"/></svg>
      <span>marisol@harborviewest.com</span>
    </li>
    <li>
      <svg viewBox="0 0 12 12"><circle cx="6" cy="6" r="5.5" fill="none" stroke="#fff" stroke-width="1"/><path d="M0.5 6 H11.5 M6 0.5 C3 3 3 9 6 11.5 M6 0.5 C9 3 9 9 6 11.5" fill="none" stroke="#fff" stroke-width="1"/></svg>
      <span>www.harborviewest.com</span>
    </li>
  </ul>
</section>

<section class="card card-back" aria-label="Business card back">
  <div class="back-wordmark">
    <p class="back-name">HARBORVIEW ESTATES LLC</p>
    <p class="back-url">www.harborviewest.com</p>
  </div>
</section>

</body>
</html>
```